KPV Datacore Solutions

We need a Logo and Website for our company based in London. We are a IT recruitment company . We provide quality resources to top IT company across UK.

Industry/Entity Type

It Company

Number of Pages Required

4 page

```html
<!DOCTYPE html>
<html lang="en">
<head>
<meta charset="utf-8">
<title>KPV Datacore Solutions – IT Recruitment</title>
<link rel="stylesheet" href="https://fonts.googleapis.com/css2?family=Raleway:wght@400;500;600&family=Open+Sans:ital,wght@0,400;0,600;1,400&display=swap">
<style>
:root{
  --blue:#1aa6d8;
  --orange:#f7941d;
  --orange-btn:#f9a11b;
  --ink:#333333;
  --brand-ink:#2b3a46;
  --rule:#dcdcdc;
  --nav-top:#47423d;
  --nav-bottom:#1e1c1a;
  --client-bg:#f2f2f2;
  --client-ink:#8c8c8c;
  --footer:#262626;
  --footer-base:#1b1b1b;
  --footer-ink:#c9c9c9;
}
*{box-sizing:border-box;margin:0;padding:0}
html,body{width:1200px;height:2192px;overflow:hidden;background:#fff}
body{position:relative;font-family:"Open Sans",Arial,sans-serif;color:var(--ink)}
.abs{position:absolute}

/* header */
.site-header{position:absolute;left:0;top:0;width:1200px;height:83px;background:#fff}
.brand{position:absolute;left:216px;top:25px;font-family:"Open Sans",Arial,sans-serif;font-size:26px;font-weight:600;color:var(--brand-ink);letter-spacing:-.3px}
.auth-btn{position:absolute;top:32px;height:32px;line-height:32px;text-align:center;color:#fff;font-family:"Raleway",Arial,sans-serif;font-size:12.5px;font-weight:600;text-transform:uppercase}
.auth-btn.login{left:807px;width:83px;background:var(--orange-btn)}
.auth-btn.signup{left:899px;width:85px;background:var(--blue)}

/* navigation */
.main-nav{position:absolute;left:0;top:83px;width:1200px;height:40px;background:linear-gradient(var(--nav-top),var(--nav-bottom))}
.main-nav a{position:absolute;top:0;height:40px;line-height:40px;color:#fff;text-decoration:none;font-family:"Raleway",Arial,sans-serif;font-size:13.5px;font-weight:500;text-transform:uppercase}
.main-nav a.active{background:var(--orange-btn);width:83px;text-align:center}

/* hero */
.hero{position:absolute;left:0;top:123px;width:1200px;height:438px;background:linear-gradient(100deg,#8a8f96 0%,#c9ccd0 28%,#e4e6e8 50%,#b9c0c8 72%,#d8dde2 100%)}
.hero-title{position:absolute;left:0;width:1200px;text-align:center;color:#fff;font-family:"Raleway",Arial,sans-serif}
.hero-title.main{top:142px;font-size:40px;font-weight:400}
.hero-title.sub{top:192px;font-size:28px;font-weight:400}
.hero-btn{position:absolute;top:247px;height:33px;line-height:31px;border:2px solid #fff;color:#fff;text-align:center;font-family:"Raleway",Arial,sans-serif;font-size:13px;font-weight:500;text-transform:uppercase}
.slider-dots{position:absolute;top:411px;left:566px;display:flex;gap:3px}
.slider-dots i{display:block;width:15px;height:15px;border-radius:50%;background:#fff}
.slider-dots i.on{background:#f2c316;border:2px solid #fff}

/* about */
.about{position:absolute;left:0;top:561px;width:1200px;height:374px}
.about h2{position:absolute;top:40px;left:0;width:1200px;text-align:center;color:#fff;font-family:"Raleway",Arial,sans-serif;font-size:27px;font-weight:400;text-transform:uppercase}
.about-text{position:absolute;left:255px;top:88px;width:720px;text-align:center;color:#fff;font-size:10.5px;line-height:17.5px}
.feature{position:absolute;top:168px;width:220px;text-align:center;color:#fff}
.feature svg{display:block;margin:0 auto}
.feature h3{margin-top:14px;font-family:"Raleway",Arial,sans-serif;font-size:18px;font-weight:400}
.feature p{margin-top:6px;font-size:10.5px;line-height:16px}

/* jobs */
.jobs-title{position:absolute;left:215px;top:982px;font-family:"Raleway",Arial,sans-serif;font-size:25px;font-weight:400;color:#333}
.more-btn{position:absolute;left:821px;top:987px;width:147px;height:29px;line-height:27px;border:1px solid #bdbdbd;text-align:center;font-size:11px;color:#555;box-shadow:0 1px 2px rgba(0,0,0,.12)}
.job-row{position:absolute;left:212px;width:764px;height:80px}
.job-row.ruled{border-bottom:1px solid var(--rule)}
.job-name{position:absolute;left:4px;top:0;font-size:14px;color:#333}
.job-sub{position:absolute;font-size:10.5px;color:var(--blue)}
.job-loc{position:absolute;left:180px;top:0;font-size:13px;color:#444}
.job-loc svg{position:absolute;left:-15px;top:1px}
.job-type{position:absolute;left:314px;top:0;font-size:13px;color:#444}
.job-qual{position:absolute;left:468px;top:0;font-size:13px;color:#444}
.job-qual-note{position:absolute;left:468px;top:22px;font-size:9.5px;color:#555}
.apply-btn{position:absolute;left:655px;top:-6px;width:92px;height:29px;line-height:29px;text-align:center;background:var(--orange);color:#fff;font-size:11.5px;font-weight:600}

/* clients */
.clients{position:absolute;left:0;top:1380px;width:1200px;height:272px;background:var(--client-bg);border-top:1px solid #e2e2e2;border-bottom:1px solid #e2e2e2}
.clients h2{position:absolute;top:45px;left:0;width:1200px;text-align:center;font-family:"Raleway",Arial,sans-serif;font-size:24px;font-weight:400;color:#666}
.client{position:absolute;width:150px;margin-left:-75px;text-align:center;font-family:"Open Sans",Arial,sans-serif;font-size:16px;font-weight:600;color:var(--client-ink);white-space:nowrap}

/* testimonials */
.testimonials h2{position:absolute;top:1676px;left:0;width:1200px;text-align:center;font-family:"Raleway",Arial,sans-serif;font-size:25px;font-weight:400;color:var(--blue)}
.avatar{position:absolute;left:555px;top:1721px;width:90px;height:90px;border-radius:50%;background:radial-gradient(circle at 50% 45%,#c9a48a,#7d6a5c 70%,#5d6d55)}
.quote{position:absolute;left:345px;top:1818px;width:520px;text-align:center;font-size:10.5px;font-style:italic;line-height:17px;color:#777}
.quote b{font-family:Georgia,serif;font-size:24px;font-style:normal;color:#444;line-height:0;position:relative;top:6px}
.quote-author{position:absolute;left:0;top:1871px;width:1200px;text-align:center;font-size:10.5px;color:#333}
.arrow{position:absolute;top:1766px}

/* footer */
.site-footer{position:absolute;left:0;top:1940px;width:1200px;height:201px;background:var(--footer)}
.footer-col{position:absolute;top:53px;color:#fff}
.footer-col h4{font-family:"Raleway",Arial,sans-serif;font-size:13px;font-weight:500;text-transform:uppercase;margin-bottom:9px}
.footer-col li{list-style:none;font-size:11px;color:var(--footer-ink);line-height:21px}
.map{position:absolute;left:474px;top:52px;width:204px;height:110px;background:linear-gradient(135deg,#d8dde0,#b8cbd6 55%,#e3e4de)}
.social{display:grid;grid-template-columns:auto auto;gap:6px 14px;margin-top:2px}
.social span{display:flex;align-items:center;gap:5px;font-size:11px;color:var(--footer-ink)}
.social span i{display:inline-block;width:12px;height:12px;border:1.5px solid #fff;border-radius:50%}
.footer-base{position:absolute;left:0;top:2141px;width:1200px;height:51px;background:var(--footer-base)}
.footer-base p{position:absolute;left:227px;top:18px;font-size:10px;color:#6d6d6d}
</style>
</head>
<body>

<header class="site-header">
  <div class="brand">KPV Datacore Solutions</div>
  <a class="auth-btn login">Log In</a>
  <a class="auth-btn signup">Sign Up</a>
</header>

<nav class="main-nav">
  <a class="active" style="left:227px">Home</a>
  <a style="left:338px">About Us</a>
  <a style="left:447px">Services</a>
  <a style="left:552px">Find Jobs</a>
  <a style="left:664px">Career</a>
  <a style="left:756px">Testimonial</a>
  <a style="left:887px">Contact</a>
</nav>

<section class="hero">
  <div class="abs" role="img" aria-label="Photo of recruiters shaking hands with a candidate in a bright office" style="inset:0;background:linear-gradient(180deg,rgba(40,45,55,.05),rgba(40,45,55,.25))"></div>
  <h1 class="hero-title main">Over 15 years of experience in</h1>
  <p class="hero-title sub">Recruitment &amp; Job Seekers</p>
  <a class="hero-btn" style="left:456px;width:139px">Apply Now</a>
  <a class="hero-btn" style="left:607px;width:137px">Career in IT</a>
  <div class="slider-dots"><i class="on"></i><i></i><i></i><i></i></div>
</section>

<section class="about">
  <svg class="abs" width="1200" height="390" style="left:0;top:0" aria-hidden="true">
    <defs>
      <linearGradient id="band" x1="0" y1="0" x2="1" y2="1">
        <stop offset="0" stop-color="#1dbdec"/>
        <stop offset="1" stop-color="#0fa6da"/>
      </linearGradient>
      <linearGradient id="shade" x1="0" y1="0" x2="0" y2="1">
        <stop offset="0" stop-color="#e8e8e8"/>
        <stop offset="1" stop-color="#ffffff"/>
      </linearGradient>
    </defs>
    <rect x="215" y="300" width="770" height="70" fill="url(#shade)"/>
    <polygon points="0,0 1200,0 1200,304 600,373 0,304" fill="url(#band)"/>
  </svg>
  <h2>About Our Company</h2>
  <p class="about-text">Ut ac mi quis lacus mollis aliquam Curabitur iaculis tempus eros Curabitur vel mi sit amet magna malesuada ultrices Ut nisi erat fermentum vel congue id euismod in elit Fusce ultricies orci ac feugiat suscipit leo massa sodales velit et scelerisque mi Class aptent taciti sociosqu ad litora torquent per conubia nostra per inceptos hymen aeos Proin nulla arcu nonummy luctus dictum eget fermentum et lorem</p>

  <div class="feature" style="left:225px">
    <svg width="66" height="56" viewBox="0 0 66 56" aria-hidden="true">
      <circle cx="27" cy="24" r="19" fill="none" stroke="#fff" stroke-width="4"/>
      <circle cx="27" cy="19" r="5" fill="#fff"/>
      <path d="M17 34 q10-12 20 0" fill="#fff"/>
      <line x1="41" y1="38" x2="55" y2="52" stroke="#fff" stroke-width="6" stroke-linecap="round"/>
    </svg>
    <h3>Recruitment</h3>
    <p>In massa libero interdum nec interdum vel blandit sed nulla In ullamcorper est ege</p>
  </div>

  <div class="feature" style="left:490px">
    <svg width="66" height="56" viewBox="0 0 66 56" aria-hidden="true">
      <g fill="none" stroke="#fff" stroke-width="2">
        <rect x="14" y="38" width="8" height="14"/>
        <rect x="26" y="30" width="8" height="22"/>
        <rect x="38" y="20" width="8" height="32"/>
        <rect x="50" y="8" width="8" height="44"/>
        <polyline points="10,32 24,18"/>
        <polyline points="17,18 24,18 24,25"/>
      </g>
    </svg>
    <h3>Career in IT Industry</h3>
    <p>In massa libero interdum nec interdum vel blandit sed nulla In ullamcorper est ege</p>
  </div>

  <div class="feature" style="left:755px">
    <svg width="66" height="56" viewBox="0 0 66 56" aria-hidden="true">
      <g fill="none" stroke="#fff" stroke-width="2">
        <rect x="22" y="4" width="30" height="38"/>
        <rect x="14" y="12" width="30" height="42" fill="#15b3e4"/>
        <rect x="19" y="18" width="10" height="10"/>
        <line x1="32" y1="20" x2="40" y2="20"/>
        <line x1="32" y1="26" x2="40" y2="26"/>
        <line x1="19" y1="34" x2="40" y2="34"/>
        <line x1="19" y1="40" x2="40" y2="40"/>
        <line x1="19" y1="46" x2="34" y2="46"/>
      </g>
    </svg>
    <h3>Apply for Job</h3>
    <p>In massa libero interdum nec interdum vel blandit sed nulla In ullamcorper est</p>
  </div>
</section>

<section class="jobs">
  <h2 class="jobs-title">Featured Jobs</h2>
  <a class="more-btn">View more Job Listings</a>

  <div class="job-row ruled" style="top:1046px;height:59px">
    <div class="job-name">Web Developer</div>
    <div class="job-sub" style="left:4px;top:21px">Disoc Info</div>
    <div class="job-loc"><svg width="11" height="16" viewBox="0 0 11 16"><path d="M5.5 0a5.5 5.5 0 0 0-5.5 5.5c0 4 5.5 10.5 5.5 10.5s5.5-6.5 5.5-10.5A5.5 5.5 0 0 0 5.5 0z" fill="#f7941d"/><circle cx="5.5" cy="5.5" r="2" fill="#fff"/></svg>New York</div>
    <div class="job-type">Full Time Job</div>
    <div class="job-sub" style="left:314px;top:21px">View full Details</div>
    <div class="job-qual">Qualification</div>
    <div class="job-qual-note">Morbi diam mauris viverra in</div>
    <a class="apply-btn">Apply Now</a>
  </div>

  <div class="job-row ruled" style="top:1127px;height:57px">
    <div class="job-name">Programmer</div>
    <div class="job-sub" style="left:4px;top:21px">Disoc Info</div>
    <div class="job-loc"><svg width="11" height="16" viewBox="0 0 11 16"><path d="M5.5 0a5.5 5.5 0 0 0-5.5 5.5c0 4 5.5 10.5 5.5 10.5s5.5-6.5 5.5-10.5A5.5 5.5 0 0 0 5.5 0z" fill="#f7941d"/><circle cx="5.5" cy="5.5" r="2" fill="#fff"/></svg>New York</div>
    <div class="job-type">Full Time Job</div>
    <div class="job-sub" style="left:314px;top:21px">View full Details</div>
    <div class="job-qual">Qualification</div>
    <div class="job-qual-note" style="color:var(--blue)">Morbi diam mauris viverra in</div>
    <a class="apply-btn">Apply Now</a>
  </div>

  <div class="job-row ruled" style="top:1208px;height:59px">
    <div class="job-name">Graphic Designer</div>
    <div class="job-sub" style="left:4px;top:21px">Disoc Info</div>
    <div class="job-loc"><svg width="11" height="16" viewBox="0 0 11 16"><path d="M5.5 0a5.5 5.5 0 0 0-5.5 5.5c0 4 5.5 10.5 5.5 10.5s5.5-6.5 5.5-10.5A5.5 5.5 0 0 0 5.5 0z" fill="#f7941d"/><circle cx="5.5" cy="5.5" r="2" fill="#fff"/></svg>New York</div>
    <div class="job-type">Full Time Job</div>
    <div class="job-sub" style="left:314px;top:21px">View full Details</div>
    <div class="job-qual">Qualification</div>
    <div class="job-qual-note" style="color:var(--blue)">Morbi diam mauris viverra in</div>
    <a class="apply-btn">Apply Now</a>
  </div>

  <div class="job-row" style="top:1289px">
    <div class="job-name">Marketing Executive</div>
    <div class="job-sub" style="left:4px;top:21px">Disoc Info</div>
    <div class="job-loc"><svg width="11" height="16" viewBox="0 0 11 16"><path d="M5.5 0a5.5 5.5 0 0 0-5.5 5.5c0 4 5.5 10.5 5.5 10.5s5.5-6.5 5.5-10.5A5.5 5.5 0 0 0 5.5 0z" fill="#f7941d"/><circle cx="5.5" cy="5.5" r="2" fill="#fff"/></svg>New York</div>
    <div class="job-type">Full Time Job</div>
    <div class="job-sub" style="left:314px;top:21px">View full Details</div>
    <div class="job-qual">Qualification</div>
    <div class="job-qual-note" style="color:var(--blue)">Morbi diam mauris viverra in</div>
    <a class="apply-btn">Apply Now</a>
  </div>
</section>

<section class="clients">
  <h2>Our Clients</h2>
  <div class="client" style="left:323px;top:104px">Brightlane</div>
  <div class="client" style="left:463px;top:104px">Hollis Group</div>
  <div class="client" style="left:600px;top:104px">Quarry Labs</div>
  <div class="client" style="left:741px;top:104px">Meridian</div>
  <div class="client" style="left:877px;top:104px">Fennick</div>
  <div class="client" style="left:323px;top:170px">Ashcombe</div>
  <div class="client" style="left:463px;top:170px">Lumen Retail</div>
  <div class="client" style="left:600px;top:170px">Oakvale Capital</div>
  <div class="client" style="left:741px;top:170px">Ledgerly</div>
  <div class="client" style="left:877px;top:170px">Skyforge</div>
</section>

<section class="testimonials">
  <h2>Testimonials</h2>
  <div class="avatar" role="img" aria-label="Portrait photo of the client giving the testimonial"></div>
  <svg class="arrow" style="left:276px" width="24" height="54" viewBox="0 0 24 54" aria-hidden="true"><polyline points="22,1 2,27 22,53" fill="none" stroke="#666" stroke-width="1.3"/></svg>
  <svg class="arrow" style="left:906px" width="24" height="54" viewBox="0 0 24 54" aria-hidden="true"><polyline points="2,1 22,27 2,53" fill="none" stroke="#666" stroke-width="1.3"/></svg>
  <p class="quote"><b>&ldquo;</b> Morbi diam mauris viverra in gravida eu mattis in ante Morbi eget arcu Morbi porta libero id ullamcorper non-ummy nibh ligula pulvinar metus eget consectetuer augue nisi quis lacus Ut ac mi quis lacus mollis aliquam Cura-bitur iaculis tempus eros Curabitur vel mi sit amet Mauris vel lacus vitae felis <b>&rdquo;</b></p>
  <p class="quote-author">By Author Name, City Location</p>
</section>

<footer class="site-footer">
  <div class="footer-col" style="left:237px">
    <h4>Company</h4>
    <ul><li>Home</li><li>About Us</li><li>Blogs</li><li>Find Jobs</li></ul>
  </div>
  <div class="footer-col" style="left:362px">
    <h4>Resources</h4>
    <ul><li>Support</li><li>Projects</li><li>Contat Us</li></ul>
  </div>
  <div class="map" role="img" aria-label="Street map showing the office location"></div>
  <div class="footer-col" style="left:699px">
    <h4>Quick Contact</h4>
    <ul><li>18 Harlow Lane</li><li>London</li><li>E9 4QT</li></ul>
  </div>
  <div class="footer-col" style="left:854px">
    <h4>Follow Us</h4>
    <div class="social">
      <span><i></i>Chirp</span>
      <span><i></i>Pagebook</span>
      <span><i></i>Linkwork</span>
      <span><i></i>Circleplus</span>
    </div>
  </div>
</footer>
<div class="footer-base"><p>© 2016 Company Name &nbsp;All right reserved &nbsp;Term of Use</p></div>

</body>
</html>
```